Where the Lantern Fades: A Sacred Wandering

This is a memoir about my breakdown/breakthrough followed by a spiritual awakening in 2012, I found my guru Harsh Omveli Dev, Mother Ayahuasca, and my spiritual mother, Ishu. By 2013, I was headed for a spiritual adventure through India, Southeast India, and Nepal which lasted 14 months. I lived in ashrams, meditated and prayed in temples,, traveled by train and bus, met many enlightened beings and interesting people. During Vipassana, I discovered my true essence- the light of my soul. It is a book of travel, romance, and spiritual growth. My idea is a road lined with temples, etc. I am walking down the road and see myself at the end of the road, facing out, with a bright star in my heart center. I see the colors in muted yellows and other earth-tone hues. Marigolds are used everywhere in the temples to adorn statues and doorways and this speaks to me. The title of the book is about finding out who I am beyond my stories and it is also about how our story will reveal to us who we really are.

Target Market(s)

Spiritual seekers, adventurers, travelers

Industry/Entity Type

Spiritual

Font styles to use
Serif
Sans Serif
Other font styles liked:
• I’m open. I like simplicity

Colors
FFC000
F8CF3A
FAE287
FDF2CF
FEFAEE

Requirements
Must have
• My name: Carla Serena Tovi, Earth tones, pastels, me or a likeness of me, room for ISBN on back cover
Nice to have
• In the photo uploads I drew an idea of what I would like, there is also the idea in the book
Should not have
• I am not a fan of bright colors and that's all I can select here. I like neutral colors, like browns, slate, creams, and whites. This reflects the dusty roads I took throughout my journey.

```html
<!DOCTYPE html>
<html lang="en">
<head>
<meta charset="utf-8">
<title>Where the Lantern Fades — Cover</title>
<link rel="stylesheet" href="https://fonts.googleapis.com/css2?family=Anton&family=Cinzel:wght@400&family=Oswald:wght@300&display=swap">
<style>
  :root {
    --page: #ffffff;
    --cover: #000000;
    --road: #5b5b5b;
    --road-line: #bdbdbd;
    --medallion: #eeebe3;
    --medallion-shade: #cfc8bc;
    --ink-light: #ece4d6;
    --traveler: #2a2a2a;
    --gold-deep: #c4832f;
    --gold-mid: #e9c47c;
    --gold-pale: #fbf0dc;
  }
  html, body {
    margin: 0;
    width: 1200px;
    height: 1200px;
    overflow: hidden;
    background: var(--page);
  }
  .book-cover {
    display: block;
    width: 1200px;
    height: 1200px;
  }
  .cover-panel { fill: var(--cover); }
  .road { fill: none; stroke: var(--road); stroke-width: 24; stroke-linejoin: round; }
  .road-centerline { fill: none; stroke: var(--road-line); stroke-width: 2; stroke-dasharray: 9 7; }
  .medallion-fill { fill: url(#medallionTone); }
  .traveler-fill { fill: var(--traveler); }
  .title-line {
    font-family: "Anton", "Oswald", sans-serif;
    font-size: 160px;
    fill: url(#goldFoil);
  }
  .subtitle {
    font-family: "Cinzel", "Cormorant", serif;
    font-size: 50px;
    fill: var(--ink-light);
    letter-spacing: 1px;
  }
  .author {
    font-family: "Oswald", sans-serif;
    font-weight: 300;
    font-size: 78px;
    fill: var(--ink-light);
    letter-spacing: 9px;
  }
</style>
</head>
<body>
<svg class="book-cover" viewBox="0 0 1500 1500" xmlns="http://www.w3.org/2000/svg">
  <defs>
    <linearGradient id="goldFoil" gradientUnits="userSpaceOnUse" x1="500" y1="150" x2="980" y2="920">
      <stop offset="0" stop-color="var(--gold-deep)"/>
      <stop offset="0.12" stop-color="var(--gold-pale)"/>
      <stop offset="0.25" stop-color="var(--gold-deep)"/>
      <stop offset="0.38" stop-color="var(--gold-mid)"/>
      <stop offset="0.5" stop-color="var(--gold-pale)"/>
      <stop offset="0.63" stop-color="var(--gold-deep)"/>
      <stop offset="0.76" stop-color="var(--gold-pale)"/>
      <stop offset="0.88" stop-color="var(--gold-mid)"/>
      <stop offset="1" stop-color="var(--gold-deep)"/>
    </linearGradient>
    <radialGradient id="medallionTone" cx="0.5" cy="0.45" r="0.6">
      <stop offset="0" stop-color="var(--medallion-shade)"/>
      <stop offset="0.75" stop-color="var(--medallion)"/>
    </radialGradient>
  </defs>

  <rect class="cover-panel" x="292" y="82" width="900" height="1350"/>

  <g class="winding-road">
    <path class="road" d="M455 82 L455 230 C455 290 480 313 540 313 L940 313 C1000 313 1035 360 1035 420 C1035 490 1000 530 940 530 L500 530 C450 530 413 580 413 633 C413 700 450 745 510 745 L920 745 C970 745 993 790 993 840 C993 900 970 935 920 935 L540 935 C480 935 437 980 437 1028 C437 1060 470 1080 470 1100 L470 1140 L940 1140"/>
    <path class="road-centerline" d="M455 82 L455 230 C455 290 480 313 540 313 L940 313 C1000 313 1035 360 1035 420 C1035 490 1000 530 940 530 L500 530 C450 530 413 580 413 633 C413 700 450 745 510 745 L920 745 C970 745 993 790 993 840 C993 900 970 935 920 935 L540 935 C480 935 437 980 437 1028 C437 1060 470 1080 470 1100 L470 1140 L940 1140"/>
  </g>

  <g class="medallion" role="img" aria-label="Faded photo: woman silhouetted in a carved temple archway">
    <circle class="medallion-fill" cx="455" cy="215" r="77"/>
  </g>
  <g class="medallion" role="img" aria-label="Faded photo: ornate temple tower">
    <circle class="medallion-fill" cx="1035" cy="420" r="77"/>
  </g>
  <g class="medallion" role="img" aria-label="Faded photo: garlanded shrine statue">
    <circle class="medallion-fill" cx="413" cy="633" r="77"/>
  </g>
  <g class="medallion" role="img" aria-label="Faded photo: golden stupa among clouds">
    <circle class="medallion-fill" cx="993" cy="840" r="77"/>
  </g>
  <g class="medallion" role="img" aria-label="Faded photo: palace gateway facade">
    <circle class="medallion-fill" cx="437" cy="1028" r="77"/>
  </g>

  <g class="traveler" role="img" aria-label="Line drawing of the author walking along the road in traditional dress">
    <rect class="traveler-fill" x="970" y="950" width="80" height="205" rx="22"/>
  </g>

  <g class="title">
    <text class="title-line" x="565" y="283" textLength="353" lengthAdjust="spacingAndGlyphs">WHERE</text>
    <text class="title-line" x="636" y="490" textLength="214" lengthAdjust="spacingAndGlyphs">THE</text>
    <text class="title-line" x="515" y="705" textLength="453" lengthAdjust="spacingAndGlyphs">LANTERN</text>
    <text class="title-line" x="545" y="908" textLength="360" lengthAdjust="spacingAndGlyphs">FADES</text>
  </g>

  <text class="subtitle" x="750" y="1238" text-anchor="middle">A SACRED WANDERING</text>
  <text class="author" x="742" y="1380" text-anchor="middle">CARLA SERENA TOVI</text>
</svg>
</body>
</html>
```